African homeware retailer needs a web page design

We need a web page design for a new homeware and accessories store based in Johannesburg, South Africa. Our store carries modern African inspired items from designers that support social development and poverty alleviation initiatives. We have a particular preference for outfits that are centred on the empowerment of women.

Our business celebrates the skill, design and product of African craft and the work of designers looking to take that forward in a socially beneficial way (creating employment, developing skills, supporting local crafts people etc). We aim to carry items and inspirations from all over the African continent.

We would like to see a design that communicates African beauty and elegance without the typical tribal references that are made in reference to African craft or art.

We would like the web page to be stylish, uncomplicated, modern, captivating and appealing to the discerning customer. A similar value proposition is that of http://www.marlowtenwick.example/.

This is an e-commerce website which must be attractive to both individual buyers and design professionals so the website needs to look professional.

Here are links to some websites we like:
http://www.quenbyhollis.example/
http://www.dravelo.example/

Our logo is attached to the brief.

Target Market(s)

Our target market is female, age 20-50. However should not alienate the design conscious male customer therefore

Industry/Entity Type

E-Commerce

Requirements
Must have
• - A featured product banner which includes a photograph and text. This should be easy to edit as we will be changing the featured product regularly
- An easily expendable products section with categories. Examples of categories could be cushions, bedding, crockery etc. Should be easy to add new categories as well as new product pictures
- Home/landing page should be uncluttered
- Should use the logo and should be easy to change the logo which we have in various colour combinations. We plan to change the logo colours depending on circumstance e.g. make it red and white around Valentines day (similar to the way Vintrel frequently changes the logo on their landing page)

```html
<!DOCTYPE html>
<html lang="en">
<head>
<meta charset="utf-8">
<title>Amara Dune – Homeware &amp; Accessories</title>
<link href="https://fonts.googleapis.com/css2?family=Montserrat:wght@400;600;700&family=Arimo:wght@400;700&family=Noto+Serif&display=swap" rel="stylesheet">
<style>
:root{
  --cream:#fcf7d6;
  --green:#4f9c4f;
  --green-text:#4a9a46;
  --grey-text:#6b6b6b;
  --dark:#222222;
  --banner-yellow:rgba(253,243,150,.85);
  --blue:#12b2ee;
  --orange:#f5651b;
  --lime:#8dd21a;
  --title-blue:#1e9ad9;
  --title-orange:#e55a1d;
  --title-green:#4c9a48;
  --rule:#dddddd;
  --band:#f8f8f8;
  --footer:#000000;
  --footer-text:#a8a8a8;
}
*{box-sizing:border-box;margin:0;padding:0}
html,body{width:1200px;height:1000px;overflow:hidden;background:#fff}
body{position:relative;font-family:"Arimo",Arial,sans-serif;color:#444}
.abs{position:absolute}
.caps{font-family:"Montserrat",Arial,sans-serif;text-transform:uppercase}

/* header */
.site-header{left:0;top:0;width:1200px;height:168px;background:var(--cream)}
.brand{left:202px;top:37px;width:130px}
.brand-mark{display:block;width:50px;height:50px;margin:0 0 30px 24px;background:var(--green)}
.brand-name{font-family:"Montserrat",sans-serif;font-weight:600;font-size:17px;letter-spacing:1px;color:var(--green-text);white-space:nowrap}
.welcome{left:700px;top:36px;font-size:8px;font-weight:600;color:#666;letter-spacing:.3px}
.welcome b{color:var(--green-text);font-size:9px;font-weight:600}
.search{left:700px;top:60px;width:125px;height:29px;background:#fff;border:1px solid #e4e4e4;font-size:7px;color:#aaa;padding:10px 8px;letter-spacing:.5px}
.search-btn{left:824px;top:60px;width:33px;height:29px;background:var(--green)}
.cart{left:868px;top:60px;width:158px;height:29px;background:#f6f6f4;border:1px solid #e2e2e2;font-size:9px;color:#666;padding:9px 7px;font-weight:600}
.cart-toggle{left:993px;top:60px;width:33px;height:29px;border-left:1px solid #e2e2e2}
.utility-nav{left:489px;top:105px;font-size:8px;color:#444;letter-spacing:.2px}
.utility-nav span{margin:0 4px;color:#888}
.header-rule{left:488px;top:128px;width:538px;height:1px;background:#d4cfae}
.main-nav{left:489px;top:141px;font-family:"Montserrat",sans-serif;font-weight:700;font-size:10px;color:var(--green-text);letter-spacing:.2px}
.main-nav a{position:absolute;white-space:nowrap;text-decoration:none;color:inherit}

/* hero */
.hero-photo-left{left:255px;top:245px;width:150px;height:190px;border-radius:40%;background:radial-gradient(circle,#f2f2f0 0%,#d9d9d6 60%,rgba(255,255,255,0) 72%)}
.hero-photo-right{left:525px;top:262px;width:360px;height:175px;border-radius:30%;background:radial-gradient(ellipse,#f4f4f2 0%,#dcdfe6 55%,rgba(255,255,255,0) 72%)}
.hero-band{left:200px;top:351px;width:826px;height:89px;background:var(--banner-yellow)}
.hero-title{left:291px;top:366px;font-family:"Arimo",sans-serif;font-weight:700;font-size:33px;color:#2b2b2b;letter-spacing:.5px}
.hero-sub{left:294px;top:401px;font-size:15px;color:#2b2b2b}
.btn{display:flex;align-items:center;justify-content:center;font-family:"Montserrat",sans-serif;font-weight:700;color:#fff;text-transform:uppercase}
.hero-cta{left:857px;top:378px;width:96px;height:34px;background:var(--green);font-size:12.5px}
.save-badge{left:854px;top:231px;width:100px;height:100px;border-radius:50%;background:var(--dark);color:#fff;text-align:center;padding-top:30px;font-size:10px;line-height:11px}
.save-badge .save{font-size:13px}
.save-badge .pct{font-size:22px}
.hero-rule{left:200px;top:455px;width:826px;height:1px;background:var(--rule)}

/* features */
.col-rule{top:490px;width:1px;height:168px;background:#e3e3e3}
.feature-photo{height:74px}
.feature-title{font-family:"Noto Serif",serif;font-weight:400;font-size:17px;white-space:nowrap}
.feature-text{font-size:9px;line-height:12px;color:#555;width:150px}
.feature-btn{width:90px;height:29px;font-size:10px}

/* info band */
.info-band{left:0;top:695px;width:1200px;height:54px;background:var(--band);border-top:1px solid #e3e3e3}
.follow{left:200px;top:714px;font-family:"Montserrat",sans-serif;font-weight:600;font-size:16px;color:#7a7a7a;letter-spacing:.3px}
.social{top:710px;width:29px;height:28px;background:#333}
.band-rule{top:709px;width:1px;height:30px;background:#dcdcdc}
.ship-title{left:518px;top:710px;font-family:"Montserrat",sans-serif;font-weight:700;font-size:11.5px;color:var(--green-text)}
.ship-sub{left:518px;top:723px;font-family:"Montserrat",sans-serif;font-weight:600;font-size:9px;color:#777}
.order{left:791px;top:716px;font-family:"Montserrat",sans-serif;font-weight:600;font-size:12px;color:#777}
.order b{color:var(--green-text);margin-left:3px;font-weight:700}

/* footer */
.site-footer{left:0;top:749px;width:1200px;height:202px;background:var(--footer)}
.footer-col{top:793px}
.footer-col h3{font-family:"Montserrat",sans-serif;font-weight:600;font-size:9.5px;color:#ddd;letter-spacing:.4px;margin-bottom:8px}
.footer-col ul{list-style:none}
.footer-col li{font-size:8px;color:var(--footer-text);line-height:15.8px}
.newsletter-input{left:835px;top:817px;width:146px;height:26px;background:#3a3a3a;font-size:7px;color:#999;padding:9px 7px}
.newsletter-btn{left:981px;top:817px;width:45px;height:26px;background:var(--green);font-size:10px}
.store-location{left:835px;top:860px;font-size:8.5px;line-height:13px;color:var(--footer-text)}
.legal-bar{left:0;top:951px;width:1200px;height:49px;background:var(--green)}
.copyright{left:200px;top:970px;font-family:"Montserrat",sans-serif;font-weight:600;font-size:7.5px;color:#fff}
.legal-links{right:174px;top:970px;font-family:"Montserrat",sans-serif;font-weight:600;font-size:7.5px;color:#fff}
</style>
</head>
<body>

<header class="abs site-header">
  <div class="abs brand">
    <span class="brand-mark"></span>
    <div class="brand-name">AMARA DUNE</div>
  </div>
  <p class="abs welcome caps">Welcome visitor you can <b>Login</b> or <b>Create an Account</b></p>
  <div class="abs search caps">Search</div>
  <div class="abs search-btn">
    <svg width="33" height="29" viewBox="0 0 33 29"><circle cx="15" cy="13" r="4" fill="none" stroke="#fff" stroke-width="2"/><line x1="18" y1="16" x2="21.5" y2="19.5" stroke="#fff" stroke-width="2.5" stroke-linecap="round"/></svg>
  </div>
  <div class="abs cart caps">Cart 0 item(s) - $0.00</div>
  <div class="abs cart-toggle">
    <svg width="33" height="29" viewBox="0 0 33 29"><polyline points="11,12 17,18 23,12" fill="none" stroke="#bbb" stroke-width="1.2"/></svg>
  </div>
  <nav class="abs utility-nav caps">Home<span>|</span>Wish List (0)<span>|</span>My Account<span>|</span>Shopping Cart<span>|</span>Checkout</nav>
  <div class="abs header-rule"></div>
  <nav class="abs main-nav">
    <a style="left:0">LOREM IPSUM</a>
    <a style="left:99px">LOREM IPSUM</a>
    <a style="left:191px">LOREM IPSUM</a>
    <a style="left:284px">LOREM IPSUM</a>
    <a style="left:383px">LOREM IPSUM</a>
  </nav>
</header>

<section class="hero">
  <div class="abs hero-photo-left" role="img" aria-label="Photograph of white plates and bowls with black floral print"></div>
  <div class="abs hero-photo-right" role="img" aria-label="Photograph of a white dinner set with blue rims, teapot and cups"></div>
  <div class="abs save-badge"><span class="save">SAVE </span><span class="pct">25%</span><br>On Selected<br>Products</div>
  <div class="abs hero-band"></div>
  <h1 class="abs hero-title">CROCKERY</h1>
  <p class="abs hero-sub">A Large Selection At Competitive Price</p>
  <a class="abs btn hero-cta">Shop Now!</a>
  <div class="abs hero-rule"></div>
</section>

<section class="features">
  <div class="abs col-rule" style="left:478px"></div>
  <div class="abs col-rule" style="left:761px"></div>

  <div class="abs feature-photo" role="img" aria-label="Photograph of a pile of colourful striped cushions" style="left:202px;top:520px;width:104px;background:linear-gradient(135deg,#e8443a,#2b4e8f 45%,#f0c23a 75%,#2a8a52);border-radius:30% 30% 20% 20%"></div>
  <h2 class="abs feature-title" style="left:317px;top:522px;color:var(--title-blue)">Home Appliance</h2>
  <p class="abs feature-text" style="left:318px;top:556px">Lorem ipsum dolor sit amet, consect-etur adipisicing elit, sed do eiusmod</p>
  <a class="abs btn feature-btn" style="left:320px;top:608px;background:var(--blue)">Learn More</a>

  <div class="abs feature-photo" role="img" aria-label="Photograph of a bed with a striped grey duvet" style="left:505px;top:527px;width:83px;height:72px;background:linear-gradient(180deg,#3a2f2a 0 18%,#d8d2cc 18% 40%,#8a8685 40%)"></div>
  <h2 class="abs feature-title" style="left:595px;top:522px;color:var(--title-orange)">Special Offer</h2>
  <p class="abs feature-text" style="left:597px;top:556px">Lorem ipsum dolor sit amet, consect-etur adipisicing elit, sed do eiusmod tempor</p>
  <a class="abs btn feature-btn" style="left:598px;top:608px;background:var(--orange)">View Detail</a>

  <div class="abs feature-photo" role="img" aria-label="Photograph of white plates with black print" style="left:779px;top:525px;width:98px;height:66px;border-radius:40%;background:radial-gradient(circle,#f2f2f2,#cfcfcf 65%,rgba(255,255,255,0) 72%)"></div>
  <h2 class="abs feature-title" style="left:881px;top:522px;color:var(--title-green)">Free Shipping</h2>
  <p class="abs feature-text" style="left:882px;top:556px">on selected lorem ipsum products &amp; home appliance</p>
  <a class="abs btn feature-btn" style="left:884px;top:608px;background:var(--lime)">Read More</a>
</section>

<section class="abs info-band"></section>
<p class="abs follow">FOLLOW US</p>
<span class="abs social" style="left:334px" aria-label="Social network"></span>
<span class="abs social" style="left:368px" aria-label="Social network"></span>
<div class="abs band-rule" style="left:477px"></div>
<p class="abs ship-title">FREE SHIPPING</p>
<p class="abs ship-sub">SHIPPING COST: On Order over $99</p>
<div class="abs band-rule" style="left:761px"></div>
<p class="abs order">ORDER ONLINE <b>TEL: 0987 6543 210</b></p>

<footer class="abs site-footer"></footer>
<div class="abs footer-col" style="left:200px">
  <h3>MY ACCOUNT</h3>
  <ul><li>Sign In</li><li>View Cart</li><li>My Wishlist</li><li>Track My Order</li><li>Help</li></ul>
</div>
<div class="abs footer-col" style="left:426px">
  <h3>SITE INFO</h3>
  <ul><li>About Us</li><li>Customer Service</li><li>Privacy Policy</li><li>Site Map</li><li>Search Terms</li><li>Advanced Search</li><li>Orders and Returns</li></ul>
</div>
<div class="abs footer-col" style="left:630px">
  <h3>WHY BUY FOR US</h3>
  <ul><li>Shipping &amp; Returns</li><li>Secure Shopping</li><li>International Shipping</li><li>Affiliates</li><li>Group Sales</li><li>Contact Us</li></ul>
</div>
<div class="abs footer-col" style="left:835px">
  <h3>NEWSLETTER</h3>
</div>
<div class="abs newsletter-input">Enter Your Email Address</div>
<a class="abs btn newsletter-btn" style="text-transform:none">Go</a>
<p class="abs store-location">Store Location: #1234, Lorem Ipsum Link<br>Lorem Ipsum, 2345</p>

<div class="abs legal-bar"></div>
<p class="abs copyright">© 2014 COMPANY NAME. ALL RIGHTS RESERVED</p>
<p class="abs legal-links">PRIVACY POLICY &nbsp;|&nbsp; TERMS &amp; CONDITIONS</p>

</body>
</html>
```